Business Cards for a law firm

Business cards for our law firm. Use our silhoette logo and OAK PARTNERS - check our website (www.oakpartners.example)

Contact Information for Business Card

our silhouette logo, OAK PARTNERS, 800-555-0147, Dorian Pemberton, dorian@oakpartners.example

Requirements
Must have
• our silhouette logo, OAK PARTNERS, 800-555-0147, Dorian Pemberton, dorian@oakpartners.example

```html
<!DOCTYPE html>
<html lang="en">
<head>
<meta charset="utf-8">
<title>Oak Partners – Business Cards</title>
<link rel="stylesheet" href="https://fonts.googleapis.com/css2?family=Tenor+Sans&display=swap">
<style>
  :root {
    --navy: #233368;
    --paper: #f0f0f0;
    --backdrop: #e2e6e7;
    --white: #ffffff;
  }
  * { box-sizing: border-box; margin: 0; padding: 0; }
  html, body {
    width: 1200px; height: 960px; overflow: hidden;
    background: var(--backdrop);
    font-family: "Tenor Sans", sans-serif;
  }
  .stage { position: relative; width: 1200px; height: 960px; }
  .card {
    position: absolute; left: 250px; width: 701px; height: 400px;
    border-radius: 28px; overflow: hidden;
  }
  .card--front { top: 60px; background: var(--navy); }
  .card--back { top: 500px; background: var(--paper); }

  .wordmark { color: var(--white); line-height: 0.92; text-transform: uppercase; }
  .card--front .wordmark {
    position: absolute; left: 0; right: 0; top: 148px;
    text-align: center; font-size: 56px; letter-spacing: 1px;
  }
  .card--back .brand-square {
    position: absolute; left: 24px; top: 42px; width: 56px; height: 56px;
    background: var(--navy);
  }
  .card--back .wordmark {
    position: absolute; left: 91px; top: 38px;
    color: var(--navy); font-size: 33px; letter-spacing: 0.5px;
  }
  .holder-name {
    position: absolute; right: 30px; top: 38px;
    color: var(--navy); font-size: 27px; font-variant: small-caps;
    letter-spacing: 1px; text-transform: lowercase;
  }
  .holder-name .first { -webkit-text-stroke: 0.9px var(--navy); }
  .holder-name::first-letter { text-transform: uppercase; }
  .holder-name .cap { text-transform: uppercase; }
  .name-tab {
    position: absolute; right: 0; top: 33px; width: 21px; height: 36px;
    background: var(--navy);
  }
  .contact-list {
    position: absolute; left: 24px; top: 302px; list-style: none;
    color: var(--navy); font-size: 16px; letter-spacing: 1px; text-transform: uppercase;
  }
  .contact-list li { display: flex; align-items: center; height: 23px; }
  .contact-list svg { width: 16px; height: 16px; margin-right: 11px; fill: var(--navy); }
  .contact-list .phone-number { font-size: 18px; text-transform: none; }
</style>
</head>
<body>
<main class="stage">
  <section class="card card--front" aria-label="Card front">
    <div class="wordmark">Oak<br>Partners</div>
  </section>

  <section class="card card--back" aria-label="Card back">
    <div class="brand-square"></div>
    <div class="wordmark">Oak<br>Partners</div>
    <div class="holder-name"><span class="first"><span class="cap">D</span>orian</span> <span class="cap">P</span>emberton</div>
    <div class="name-tab"></div>

    <ul class="contact-list">
      <li>
        <svg viewBox="0 0 16 16" aria-hidden="true"><path d="M3.5 1.5l2.5 3-1.5 1.6c.8 1.9 2.3 3.4 4.2 4.3l1.6-1.5 3 2.5-1.6 2.6C7 14 2 9 .9 3.1z"/></svg>
        <span class="phone-number">800-555-0147</span>
      </li>
      <li>
        <svg viewBox="0 0 16 16" aria-hidden="true"><path d="M8 1a7 7 0 100 14A7 7 0 008 1zm0 1.5c.9 0 1.9 1.6 2.2 4.5H5.8C6.1 4.1 7.1 2.5 8 2.5zM2.6 8.5h1.9c.1 1.5.4 2.8.9 3.8a5.5 5.5 0 01-2.8-3.8zm0-1.5a5.5 5.5 0 012.8-3.8c-.5 1-.8 2.3-.9 3.8zM8 13.5c-.9 0-1.9-1.6-2.2-5h4.4c-.3 3.4-1.3 5-2.2 5zm2.6-1.2c.5-1 .8-2.3.9-3.8h1.9a5.5 5.5 0 01-2.8 3.8zM11.5 7c-.1-1.5-.4-2.8-.9-3.8A5.5 5.5 0 0113.4 7z"/></svg>
        <span>www.oakpartners.example</span>
      </li>
      <li>
        <svg viewBox="0 0 16 16" aria-hidden="true"><path d="M1 5l7-4 7 4v10H1zm1.5 1.2v7.3h11V6.2L8 9.6z"/></svg>
        <span>dorian@oakpartners.example</span>
      </li>
    </ul>
  </section>
</main>
</body>
</html>
```